Modern Business Card For A Digital Advertising Company

I'll be print on the Pell Prints Velour paper http://us.pellprints.com/products/velour/business-cards.html
Need's to be modern and use the color palette of the logo or gray scales. I think integrating the pixelation of the logo in to the card and having it wrap from one side to the other could be interesting. My company provides ad operations, web development, and number of other services to websites around the world. You can see my website at http://www.zantorhq.com
Contact info on the card needs to have
Owen Lasko
President
p.318.204.6637
owen@zantorhq.com
http://www.zantorhq.com
Doesn't necessarily need to be in that order
Website owners
Business

```html
<!DOCTYPE html>
<html lang="en">
<head>
<meta charset="utf-8">
<title>Zantor — Business Card</title>
<link rel="stylesheet" href="https://fonts.googleapis.com/css2?family=Open+Sans:wght@400;600;700&family=Tinos:wght@400;700&display=swap">
<style>
  :root {
    --stage: #2a2a2a;
    --card: #ffffff;
    --green: #8cc63f;
    --green-dark: #5b8f2a;
    --ink: #333333;
    --rule: #6d6d6d;
  }
  * { margin: 0; padding: 0; box-sizing: border-box; }
  html, body { width: 1200px; height: 757px; overflow: hidden; }
  body {
    background: var(--stage);
    position: relative;
    font-family: "Tinos", "Times New Roman", serif;
    color: var(--ink);
  }
  .card {
    position: absolute;
    top: 228px;
    width: 520px;
    height: 300px;
    background: var(--card);
  }
  .card--front { left: 60px; }
  .card--back { left: 620px; }

  .brand {
    position: absolute;
    left: 0; right: 0;
    display: flex;
    align-items: center;
    justify-content: center;
    gap: 10px;
    font-family: "Open Sans", Arial, sans-serif;
    font-weight: 700;
    color: var(--green);
    letter-spacing: 2px;
  }
  .brand__square { background: var(--green); display: block; }
  .card--front .brand { top: 44px; font-size: 38px; }
  .card--front .brand__square { width: 34px; height: 34px; }

  .name-band {
    position: absolute;
    left: 0; right: 0;
    top: 150px;
    height: 50px;
    border-top: 1px solid var(--rule);
    border-bottom: 1px solid var(--rule);
    padding: 4px 0;
  }
  .name-band__fill {
    height: 100%;
    background: linear-gradient(90deg, var(--green-dark), var(--green) 55%, var(--green));
    display: flex;
    align-items: center;
    justify-content: center;
    color: #fff;
  }
  .name-band__name { font-size: 22px; font-weight: 700; }
  .name-band__title { font-size: 17px; margin-left: 6px; }

  .contact {
    position: absolute;
    left: 0; right: 0;
    top: 218px;
    text-align: center;
    font-size: 16px;
    line-height: 26px;
  }
  .contact__row { display: flex; justify-content: center; align-items: center; gap: 14px; }
  .contact__item { display: inline-flex; align-items: center; gap: 5px; }
  .contact__icon { width: 12px; height: 12px; fill: var(--ink); }

  .card--back .brand { top: 70px; font-size: 44px; }
  .card--back .brand__square { width: 40px; height: 40px; }
  .services {
    position: absolute;
    left: 0; right: 0;
    top: 150px;
    text-align: center;
    font-family: "Open Sans", Arial, sans-serif;
  }
  .services__title { font-size: 24px; font-weight: 700; letter-spacing: 2px; color: #444; margin-bottom: 6px; }
  .services__list { list-style: none; font-size: 15px; line-height: 22px; color: var(--ink); }
  .services__list li span + span { margin-left: 14px; }
  .services__list span::before { content: "•"; color: var(--green); margin-right: 5px; }
</style>
</head>
<body>
  <section class="card card--front">
    <div class="brand"><span class="brand__square"></span>ZANTOR</div>
    <div class="name-band">
      <div class="name-band__fill">
        <span class="name-band__name">Owen Lasko,</span>
        <span class="name-band__title">President</span>
      </div>
    </div>
    <div class="contact">
      <div class="contact__row">
        <span class="contact__item">
          <svg class="contact__icon" viewBox="0 0 12 12" aria-hidden="true"><path d="M2.5 0.5l2 2.5-1.2 1.3c.7 1.6 1.8 2.7 3.4 3.4L8 6.5l2.5 2-1 2.5C5 10.5 1.5 7 1 2.5z"/></svg>
          318.204.6637
        </span>
        <span class="contact__item">
          <svg class="contact__icon" viewBox="0 0 12 12" aria-hidden="true"><rect x="0.5" y="2.5" width="11" height="7.5" rx="1"/><path d="M1 3l5 4 5-4" stroke="#fff" stroke-width="1.2" fill="none"/></svg>
          owen@zantorhq.com
        </span>
      </div>
      <div class="contact__row">
        <span class="contact__item">
          <svg class="contact__icon" viewBox="0 0 12 12" aria-hidden="true"><circle cx="6" cy="6" r="5.5"/><path d="M0.5 6h11M6 0.5c-2.5 3-2.5 8 0 11M6 0.5c2.5 3 2.5 8 0 11" stroke="#fff" stroke-width="0.8" fill="none"/></svg>
          www.zantorhq.com
        </span>
      </div>
    </div>
  </section>

  <section class="card card--back">
    <div class="brand"><span class="brand__square"></span>ZANTOR</div>
    <div class="services">
      <h2 class="services__title">Services</h2>
      <ul class="services__list">
        <li><span>Ad Operations</span><span>Web Development</span></li>
        <li><span>Hosting</span><span>Site Speed</span></li>
        <li><span>Social Media</span></li>
        <li><span>Search Engine Optimization</span></li>
      </ul>
    </div>
  </section>
</body>
</html>
```